Business card design needed

Double sided
Color, unique, elegant

Maybe put this quote somewhere?? But I think it might make it to cluttered?
“The Pilates Method of Body
Conditioning develops the body
uniformly, corrects posture, restores
vitality, invigorates the mind and
elevates the spirit”
- Walter Brennick

Industry/Entity Type

Business

Contact Information for Business Card

Marta Kovalenko
Pilates Instructor & Personal trainer
Mobile: 0498265043
www.qorvith.com.au
email: qorvithwell.motion@mailvex.com

```html
<!DOCTYPE html>
<html lang="en">
<head>
<meta charset="utf-8">
<title>Qorvith Health and Fitness – Business Card</title>
<link rel="stylesheet" href="https://fonts.googleapis.com/css2?family=Crimson+Text:wght@400;700&family=Kalam:wght@700&display=swap">
<style>
  :root {
    --bg: #ecebe8;
    --card: #ffffff;
    --green: #86c874;
    --green-text: #5fb24a;
    --purple: #c476bd;
    --purple-text: #b25aab;
    --grey: #555555;
    --photo-a: linear-gradient(135deg, #e9dcd2, #b9a39a 60%, #6b7fc4);
    --photo-b: linear-gradient(135deg, #f3ece6, #d9b8a4 55%, #c8463f);
    --serif: "Crimson Text", Georgia, serif;
    --script: "Kalam", cursive;
  }
  * { box-sizing: border-box; margin: 0; padding: 0; }
  html, body { width: 1200px; height: 740px; overflow: hidden; }
  body { background: var(--bg); font-family: var(--serif); position: relative; }

  .card {
    position: absolute; top: 215px; width: 540px; height: 310px;
    background: var(--card); overflow: hidden;
    box-shadow: 0 4px 14px rgba(0,0,0,.15);
  }
  .card--front { left: 40px; }
  .card--back { left: 620px; }
  .band { position: absolute; left: 0; right: 0; }
  .band--top { top: 0; height: 10px; background: var(--green); }
  .band--bottom { bottom: 0; height: 12px; background: var(--purple); }

  .brand { position: absolute; display: flex; align-items: center; gap: 8px; }
  .brand__dot { width: 14px; height: 14px; border-radius: 50%; background: var(--green); }
  .brand__name { font-family: var(--serif); font-weight: 400; color: var(--grey); letter-spacing: 3px; }

  /* front */
  .card--front .brand { left: 40px; top: 135px; }
  .card--front .brand__name { font-size: 40px; }
  .divider { position: absolute; left: 268px; top: 26px; width: 2px; height: 236px; background: var(--purple); }
  .bubble { position: absolute; left: 285px; top: 22px; width: 240px; height: 190px; }
  .quote {
    position: absolute; left: 300px; top: 38px; width: 210px;
    color: var(--purple-text); font-size: 15px; line-height: 1.3; text-align: center;
  }
  .signature {
    position: absolute; right: 30px; top: 222px;
    font-family: var(--script); font-size: 22px; color: var(--purple-text);
  }

  /* back */
  .frame { position: absolute; border: 1.5px solid var(--purple); border-radius: 6px; background: var(--card); }
  .frame--logo { left: 165px; top: 70px; width: 175px; height: 110px; display: flex; align-items: center; justify-content: center; }
  .frame--logo .brand { position: static; }
  .frame--logo .brand__name { font-size: 30px; }
  .frame--photo { padding: 6px; }
  .frame--photo-top { left: 322px; top: 26px; width: 190px; height: 118px; }
  .frame--photo-bottom { left: 300px; top: 140px; width: 178px; height: 96px; }
  .photo { width: 100%; height: 100%; border-radius: 3px; }
  .photo--weights { background: var(--photo-a); }
  .photo--stretch { background: var(--photo-b); }

  .person { position: absolute; left: 22px; top: 186px; }
  .person__name { font-size: 22px; font-weight: 700; color: var(--purple-text); line-height: 1; }
  .person__role { font-size: 13px; font-weight: 700; color: var(--green-text); margin-top: 2px; }
  .contacts { position: absolute; left: 22px; top: 232px; list-style: none; }
  .contacts li { display: flex; align-items: center; gap: 8px; font-size: 12px; color: var(--purple-text); height: 19px; }
  .contacts svg { width: 14px; height: 14px; flex: none; }
</style>
</head>
<body>

<section class="card card--front" aria-label="Card front">
  <div class="band band--top"></div>
  <div class="brand">
    <span class="brand__dot"></span>
    <span class="brand__name">Qorvith</span>
  </div>
  <div class="divider"></div>
  <svg class="bubble" viewBox="0 0 240 190" aria-hidden="true">
    <path d="M14 2 H226 Q238 2 238 14 V150 Q238 162 226 162 H212 L226 186 L190 162 H14 Q2 162 2 150 V14 Q2 2 14 2 Z"
          fill="none" stroke="var(--purple)" stroke-width="1.5"/>
  </svg>
  <p class="quote">“The Pilates Method of Body Conditioning develops the body uniformly, corrects posture, restores vitality, invigorates the mind and elevates the spirit”</p>
  <p class="signature">Walter Brennick</p>
  <div class="band band--bottom"></div>
</section>

<section class="card card--back" aria-label="Card back">
  <div class="band band--top"></div>
  <div class="frame frame--photo frame--photo-top">
    <div class="photo photo--weights" role="img" aria-label="Photo of a woman training with hand weights"></div>
  </div>
  <div class="frame frame--photo frame--photo-bottom">
    <div class="photo photo--stretch" role="img" aria-label="Photo of a woman in a side plank stretch"></div>
  </div>
  <div class="frame frame--logo">
    <div class="brand">
      <span class="brand__dot"></span>
      <span class="brand__name">Qorvith</span>
    </div>
  </div>

  <div class="person">
    <p class="person__name">Marta Kovalenko</p>
    <p class="person__role">Pilates Instructor &amp; Personal trainer</p>
  </div>
  <ul class="contacts">
    <li>
      <svg viewBox="0 0 14 14" aria-hidden="true"><rect width="14" height="14" rx="3" fill="var(--purple)"/><path d="M4 3 L6 3 L6.5 5 L5.5 6 Q6.5 8 8 8.5 L9 7.5 L11 8 L11 10 Q7 11 4 7 Q3 5 4 3 Z" fill="#fff"/></svg>
      0498265043
    </li>
    <li>
      <svg viewBox="0 0 14 14" aria-hidden="true"><rect width="14" height="14" rx="3" fill="var(--purple)"/><rect x="2.5" y="4" width="9" height="6.5" fill="none" stroke="#fff" stroke-width="1"/><path d="M2.5 4 L7 8 L11.5 4" fill="none" stroke="#fff" stroke-width="1"/></svg>
      qorvithwell.motion@mailvex.com
    </li>
    <li>
      <svg viewBox="0 0 14 14" aria-hidden="true"><circle cx="7" cy="7" r="7" fill="var(--purple)"/><g fill="none" stroke="#fff" stroke-width=".9"><circle cx="7" cy="7" r="4.5"/><ellipse cx="7" cy="7" rx="2" ry="4.5"/><path d="M2.5 7 H11.5"/></g></svg>
      www.qorvith.com.au
    </li>
  </ul>
  <div class="band band--bottom"></div>
</section>

</body>
</html>
```